Tovimar Community Development Planning New web site

Design a new web site. I have a budget of $1,500.00.
Attached on PowerPoint is a complete site plan. Home page and linked pages.
10 - 12 pages. All copy and photos will be supplied. (300dpi)
I have shown them the concept which they like.
No data bases required. Home page with animations dissolving.
They former web site has been taken down. They have been in business 30 years in New Jersey
Colors teal blues and greens
There will be a new logo)being designed)
The text in home page copy will give you a detailed story what they are all about.

files have been approved for Tovimar, Inc.   Brenton is the designer

```html
<!DOCTYPE html>
<html lang="en">
<head>
<meta charset="utf-8">
<title>Tovimar — Community Development Planning</title>
<link href="https://fonts.googleapis.com/css2?family=Source+Sans+3:ital,wght@0,400;0,600;0,700;1,400&display=swap" rel="stylesheet">
<style>
:root{
  --ink-dark:#263238;
  --ink-darker:#222b30;
  --brand-green:#6cd34c;
  --text:#333a3f;
  --muted:#6d7275;
  --soft-bg:#f7f7f7;
  --line:#d9dcde;
  --quote-bg:#ececec;
  --white:#ffffff;
  --badge:#c9cbcc;
}
*{margin:0;padding:0;box-sizing:border-box}
html,body{width:1200px;height:2339px;overflow:hidden}
body{font-family:"Source Sans 3",Arial,sans-serif;color:var(--text);background:var(--white);position:relative}
.abs{position:absolute}

/* header */
.site-header{left:0;top:0;width:1200px;height:104px;background:var(--ink-dark)}
.brand{left:74px;top:34px;font-size:32px;font-weight:700;color:var(--brand-green);letter-spacing:1px}
.nav a{position:absolute;top:44px;color:var(--white);font-size:11.5px;font-weight:700;text-decoration:none;letter-spacing:.2px;white-space:nowrap}
.nav .active{left:374px;top:37px;width:90px;height:26px;background:var(--white);color:var(--brand-green);text-align:center;line-height:26px;border-radius:2px}
.nav .active::after{content:"";position:absolute;left:40px;bottom:-6px;border:5px solid transparent;border-top-color:var(--white);border-bottom:0}

/* hero */
.hero{left:0;top:104px;width:1200px;height:513px;background:linear-gradient(180deg,#7aa3c8 0%,#b9cde0 30%,#e2e4e2 48%,#a8a39b 65%,#4f6a3a 85%,#3f5a2e 100%)}
.hero-tag{left:150px;top:171px;width:394px;height:48px;background:var(--brand-green);color:var(--white);font-size:21px;font-weight:600;padding-left:18px;line-height:48px}
.hero-sub{left:150px;top:229px;width:366px;height:48px;background:var(--white);color:#555;font-size:21px;padding-left:18px;line-height:48px}

/* intro */
.intro{left:0;top:617px;width:1200px;height:263px;background:var(--soft-bg);border-bottom:1px solid #e6e6e6;text-align:center}
.intro h1{margin-top:42px;font-size:26px;font-weight:600;color:#333}
.rule{width:38px;height:1px;background:var(--line);margin:16px auto 18px}
.intro p{font-size:17.5px;color:var(--muted);line-height:28px}
.btn{display:inline-block;margin-top:20px;background:var(--brand-green);color:var(--white);font-size:12.5px;font-weight:700;padding:9px 16px;border-radius:2px}

/* specialities */
.section-title{font-size:20px;font-weight:700;color:#333}
.spec-item .icon{position:absolute;left:0;top:2px}
.spec-item h3{position:absolute;left:72px;top:0;font-size:17.5px;font-weight:700;color:#333;white-space:nowrap}
.spec-item .short-rule{position:absolute;left:72px;top:36px;width:38px;height:1px;background:var(--line)}
.spec-item p{position:absolute;left:72px;top:52px;width:372px;font-size:12.5px;line-height:22px;color:#555}

/* results band */
.results{left:0;top:1354px;width:1200px;height:483px;background:var(--ink-dark)}
.band-title{font-size:17.5px;font-weight:700;color:var(--white)}
.profile-text{width:468px;font-size:12.5px;line-height:15.5px;color:var(--white)}
.profile-rule{width:292px;height:1px;background:#4b5961}
.seal{left:117px;top:1627px}
.seal-note{left:233px;top:1645px;font-size:12.5px;line-height:16px;text-transform:uppercase;color:var(--white)}
.results-list{list-style:none;width:450px;font-size:12.5px;line-height:15.5px;color:var(--white)}
.results-list li{position:relative;padding-left:21px;margin-bottom:14px}
.results-list li svg{position:absolute;left:0;top:3px}
.results-list .strong{font-weight:700}
.contact-note{left:628px;top:1734px;font-size:12.5px;line-height:15.5px;text-transform:uppercase;color:var(--white)}
.contact-lines{left:925px;top:1730px;font-size:12.5px;line-height:26px;color:var(--white)}
.contact-lines div{display:flex;align-items:center;gap:14px}

/* testimonials */
.quote{width:293px;height:88px;background:var(--quote-bg);padding:13px 22px;font-size:12.5px;line-height:20.5px;color:#555}
.quote::after{content:"";position:absolute;right:30px;bottom:-14px;border-left:16px solid transparent;border-top:14px solid var(--quote-bg)}
.author{width:293px;text-align:right;font-size:11.5px;line-height:16px}
.author b{display:block;font-weight:700;color:#444;letter-spacing:.4px}
.author i{color:#666}

/* members */
.members{left:0;top:2176px;width:1200px;height:94px;background:var(--soft-bg)}
.members-label{left:117px;top:2208px;font-size:19px;font-weight:700;color:#333}
.badge{background:var(--badge)}

/* footer */
.site-footer{left:0;top:2270px;width:1200px;height:69px;background:var(--ink-darker);color:#dfe3e5;font-size:12px;text-align:center;line-height:69px}
</style>
</head>
<body>

<header class="abs site-header">
  <div class="abs brand">TOVIMAR</div>
  <nav class="nav">
    <a class="active" href="#">HOME</a>
    <a style="left:491px" href="#">OUR COMPANY</a>
    <a style="left:602px" href="#">SERVICES</a>
    <a style="left:682px" href="#">HOUSING REHAB APPLICATION</a>
    <a style="left:873px" href="#">AFFORDABLE APPLICATION</a>
    <a style="left:1057px" href="#">CONTACT US</a>
  </nav>
</header>

<section class="abs hero" role="img" aria-label="Photo of a row of restored Victorian houses with porches and a black iron fence"></section>
<div class="abs hero-tag">Cedarbrook Community Members</div>
<div class="abs hero-sub">Apply today for your rehab grant!</div>

<section class="abs intro">
  <h1>We help communities in sustainable development</h1>
  <div class="rule"></div>
  <p>Lorem ipsum dolor sit amet, consectetur adipiscing elit. Pellentesque lobortis accumsan ipsum eu feugiat.<br>Nam vehicula lacus nec magna aliquet a consequat quam tincidunt.</p>
  <span class="btn">See Our Services</span>
</section>

<h2 class="abs section-title" style="left:117px;top:920px">We specialize in</h2>

<div class="abs spec-item" style="left:128px;top:993px">
  <svg class="icon" width="40" height="40" viewBox="0 0 40 40" fill="none" stroke="#9aa0a3" stroke-width="2"><path d="M6 30 L26 10 L32 16 L12 36 L5 37 Z"/><path d="M30 30 L10 10 L6 14 L26 34 Z"/></svg>
  <h3>Community Development Planning</h3><div class="short-rule"></div>
  <p>Lorem ipsum dolor sit amet, consectetur adipiscing elit. ellentesque lobortis accumsan ipsum eu feugiat. Nam vehicula lacus nec magna aliquet a consequat quam tincidunt. Curabitur</p>
</div>
<div class="abs spec-item" style="left:630px;top:993px">
  <svg class="icon" width="40" height="42" viewBox="0 0 40 42" fill="none" stroke="#9aa0a3" stroke-width="2"><rect x="6" y="6" width="26" height="32" rx="2"/><rect x="13" y="2" width="12" height="7"/><path d="M12 24 l6 6 l10 -12"/></svg>
  <h3>Housing Rehabilitation Administration</h3><div class="short-rule"></div>
  <p>Lorem ipsum dolor sit amet, consectetur adipiscing elit. Pellente lobortis accumsan ipsum eu feugiat. Nam vehicula lacus nec magna aliquet a consequat quam tincidunt.</p>
</div>
<div class="abs spec-item" style="left:120px;top:1155px">
  <svg class="icon" width="56" height="46" viewBox="0 0 56 46" fill="none" stroke="#9aa0a3" stroke-width="2"><path d="M4 44V14M12 44V6M20 44V10M28 44V2M36 44V10M44 44V6M52 44V14"/></svg>
  <h3 style="left:80px">FHRO Program Management</h3><div class="short-rule" style="left:80px"></div>
  <p style="left:80px">Lorem ipsum dolor sit amet, consectetur adipiscing elit. ellentesque lobortis accumsan ipsum eu feugiat. Nam vehicula lacus nec magna aliquet a consequat quam tincidunt. Curabitur</p>
</div>
<div class="abs spec-item" style="left:616px;top:1155px">
  <svg class="icon" width="56" height="44" viewBox="0 0 56 44" fill="none" stroke="#9aa0a3" stroke-width="2"><path d="M4 18 L28 4 L52 18"/><rect x="6" y="20" width="44" height="22"/></svg>
  <h3 style="left:86px">SCFH programs implementation</h3><div class="short-rule" style="left:86px"></div>
  <p style="left:86px">Lorem ipsum dolor sit amet, consectetur adipiscing elit. Pellente lobortis accumsan ipsum eu feugiat. Nam vehicula lacus nec magna aliquet a consequat quam tincidunt. Curabitur</p>
</div>

<section class="abs results"></section>
<h2 class="abs band-title" style="left:117px;top:1398px">Company profile</h2>
<p class="abs profile-text" style="left:117px;top:1458px">Tovimar Inc. is a city planning firm that specializes in community development and housing rehabilitation program planning, design and implementation. We have over twenty years of experience in developing and administering income base housing and programs in accordance with the Federal Housing Renewal Office (FHRO) and State Council on Fair Housing (SCFH) rules and regulations. In addition, our firm is capable of providing the technical and administrative assistance our clients require for implementation of their income based housing programs.</p>
<div class="abs profile-rule" style="left:117px;top:1582px"></div>
<svg class="abs seal" width="78" height="78" viewBox="0 0 78 78" role="img" aria-label="Federal housing office seal"><circle cx="39" cy="39" r="37" fill="none" stroke="#fff" stroke-width="2"/></svg>
<p class="abs seal-note">To find out more about federal<br>housing programs that we will<br>administer please go to:<br><span style="text-transform:none">www.fedhousinginfo.org</span></p>

<h2 class="abs band-title" style="left:626px;top:1398px">We get results</h2>
<ul class="abs results-list" style="left:626px;top:1455px">
  <li><svg width="10" height="9" viewBox="0 0 10 9"><path d="M1 5 l3 3 l5 -7" fill="none" stroke="#6cd34c" stroke-width="1.8"/></svg>Tovimar designs income based programs to be supported by federal placement lotteries state funding.</li>
  <li><svg width="10" height="9" viewBox="0 0 10 9"><path d="M1 5 l3 3 l5 -7" fill="none" stroke="#6cd34c" stroke-width="1.8"/></svg>We implement local programs to benefit people seeking access to affordable housing.</li>
  <li><svg width="10" height="9" viewBox="0 0 10 9"><path d="M1 5 l3 3 l5 -7" fill="none" stroke="#6cd34c" stroke-width="1.8"/></svg>Our experienced staff screen applicants for local affordable housing.</li>
  <li><svg width="10" height="9" viewBox="0 0 10 9"><path d="M1 5 l3 3 l5 -7" fill="none" stroke="#6cd34c" stroke-width="1.8"/></svg>We pre-qualify persons who have applied for housing rehabilitation.</li>
  <li class="strong"><svg width="10" height="9" viewBox="0 0 10 9"><path d="M1 5 l3 3 l5 -7" fill="none" stroke="#6cd34c" stroke-width="1.8"/></svg>Conduct placement lotteries</li>
  <li><svg width="10" height="9" viewBox="0 0 10 9"><path d="M1 5 l3 3 l5 -7" fill="none" stroke="#6cd34c" stroke-width="1.8"/></svg>Through local housing rehabilitation programs, our experience construction inspectors determine what improvements are required at eligible units based on local building codes and health and safety issues.</li>
</ul>
<p class="abs contact-note">For more information about our services,<br>please contact us today at Tovimar:</p>
<div class="abs contact-lines">
  <div><svg width="12" height="18" viewBox="0 0 12 18"><rect x="1" y="1" width="10" height="16" rx="2" fill="none" stroke="#fff" stroke-width="1.5"/><circle cx="6" cy="14" r="1" fill="#fff"/></svg>(555) 214 3890</div>
  <div><span style="font-weight:700;width:12px">@</span>hello@tovimar-planning.com</div>
</div>

<h2 class="abs section-title" style="left:117px;top:1887px;font-size:18px">Testimonials</h2>
<div class="abs quote" style="left:117px;top:1955px">Nullam quis risus eget urna mollis ornare vel eu leo. Maecenas faucibus mollis interdum. Nulla vitae elit libero, a pharetra augue.</div>
<div class="abs author" style="left:104px;top:2077px"><b>JOHN MALCOLM DOE</b><i>Major of Dream City</i></div>
<div class="abs quote" style="left:476px;top:1955px">Nullam quis risus eget urna mollis ornare vel eu leo. Maecenas faucibus mollis interdum. Nulla vitae elit libero, a pharetra augue.</div>
<div class="abs author" style="left:463px;top:2077px"><b>JOHN MALCOLM DOE</b><i>Major of Dream City</i></div>
<div class="abs quote" style="left:833px;top:1955px">Nullam quis risus eget urna mollis ornare vel eu leo. Maecenas faucibus mollis interdum. Nulla vitae elit libero, a pharetra augue.</div>
<div class="abs author" style="left:820px;top:2077px"><b>JOHN MALCOLM DOE</b><i>Major of Dream City</i></div>

<section class="abs members"></section>
<div class="abs members-label">Tovimar is a member of:</div>
<div class="abs badge" role="img" aria-label="Partner association badge" style="left:427px;top:2208px;width:152px;height:26px"></div>
<div class="abs badge" role="img" aria-label="Partner association badge" style="left:661px;top:2198px;width:48px;height:46px"></div>
<div class="abs badge" role="img" aria-label="Partner association badge" style="left:826px;top:2194px;width:38px;height:48px;border-radius:50%"></div>
<div class="abs badge" role="img" aria-label="Partner association badge" style="left:950px;top:2206px;width:178px;height:30px"></div>

<footer class="abs site-footer">Copy Right 2014 Tovimar, 28 Harbor Lane, Maple Point, New Jersey, 08100 &nbsp;TEL (555) 214-3890 Fax (555) 214-3891</footer>

</body>
</html>
```